Business cards for Norwegian software consultancy business

We are in need of business cards for our Norwegian consultancy company.
“Valto Brindex AS” specializes in software development, architecture and agile methodology, providing mostly on-site services at customers.
The cards should reflect a certain level of business professionalism with an elegant touch, while paying tribute to our modern and technological heritage. Our logo should be featured, as well as room for basic information about the cardholder and legal information of the company (company name, address and VAT number).
We would like our cards to reflect that we are a modern consulting company. It should present a professional image that people will remember. The texture and color pallette should reflect our professionalism and reliability, so we prefer a light color pallette with colors such as gray, white, blue and black. The number of colors used should however not be overwhelming, with the text being distinct and readable.
We are open to untraditional layouts and playful designs as long as they communicate the intent stated above.
You could also take a look at our website http://www.brindex.no for input on our visual profile.
Our logo is attached in the form of vectors and rasterized PNG. Please comment if you would like the black-white and/or inverted versions as well.
Industry/Entity Type
Architecture
Contact Information for Business Card
Company information:
Valto Brindex AS
Kvernlia 14, 3170 Sem
482 71 519
info@brindex.no
www.brindex.no
Employee information:
Full name
Title
Email
Phone
Font styles to use
Look and feel

```html
<!DOCTYPE html>
<html lang="en">
<head>
<meta charset="utf-8">
<title>Valto Brindex AS — Business Card</title>
<link rel="stylesheet" href="https://fonts.googleapis.com/css2?family=Lato:wght@300;400;700&display=swap">
<style>
  :root {
    --backdrop: #d9dadc;
    --card-white: #ffffff;
    --ink-dark: #3a3b3d;
    --panel-dark: #333436;
    --accent-blue: #7fadd4;
    --accent-blue-deep: #6f9fc9;
    --ink-light: #ffffff;
  }
  * { box-sizing: border-box; margin: 0; padding: 0; }
  html, body {
    width: 1200px; height: 900px; overflow: hidden;
    background: var(--backdrop);
    font-family: "Lato", Arial, sans-serif;
  }
  .business-card {
    position: absolute; left: 150px; top: 180px;
    width: 900px; height: 540px;
    background: var(--card-white);
    box-shadow: 0 20px 50px rgba(0,0,0,0.18);
    overflow: hidden;
  }
  .brand {
    position: absolute; left: 0; right: 0; top: 92px;
    display: flex; justify-content: center; align-items: center; gap: 22px;
  }
  .brand-square {
    width: 46px; height: 46px; background: var(--accent-blue);
  }
  .brand-name {
    font-weight: 300; font-size: 56px; letter-spacing: 4px;
    color: var(--ink-dark); text-transform: uppercase; line-height: 1;
  }
  .contact-panel {
    position: absolute; left: 430px; top: 205px;
    width: 470px; height: 205px;
    background: var(--panel-dark);
    padding: 34px 0 0 90px;
  }
  .contact-panel::before {
    content: ""; position: absolute; left: -16px; top: 86px;
    border-top: 16px solid transparent; border-bottom: 16px solid transparent;
    border-right: 16px solid var(--panel-dark);
  }
  .contact-list { list-style: none; }
  .contact-item {
    display: flex; align-items: center; gap: 16px;
    color: var(--ink-light); font-size: 24px; font-weight: 400;
    line-height: 34px; letter-spacing: 0.5px;
  }
  .contact-icon { width: 20px; height: 20px; flex: none; }
  .holder-panel {
    position: absolute; left: 0; top: 280px;
    width: 430px; height: 185px;
    background: linear-gradient(180deg, var(--accent-blue), var(--accent-blue-deep));
    display: flex; flex-direction: column; align-items: center; justify-content: center;
    color: var(--ink-light);
  }
  .holder-panel::before {
    content: ""; position: absolute; left: 172px; top: -15px;
    border-left: 15px solid transparent; border-right: 15px solid transparent;
    border-bottom: 15px solid var(--accent-blue);
  }
  .holder-name { font-size: 34px; font-weight: 400; }
  .holder-title { font-size: 17px; font-weight: 400; letter-spacing: 1px; text-transform: uppercase; }
  .company-line {
    position: absolute; right: 30px; top: 422px;
    font-size: 24px; color: var(--ink-dark); font-weight: 400;
  }
  .company-line .company-accent { color: var(--accent-blue-deep); }
</style>
</head>
<body>
  <main class="business-card">
    <header class="brand">
      <span class="brand-square"></span>
      <span class="brand-name">Valto Brindex</span>
    </header>

    <section class="contact-panel">
      <ul class="contact-list">
        <li class="contact-item">
          <svg class="contact-icon" viewBox="0 0 20 20" aria-hidden="true"><path d="M4 2l4 1 1 4-2 2c1 2 3 4 5 5l2-2 4 1 1 4-2 2C9 19 1 11 2 4z" fill="#fff"/></svg>
          <span>482 71 519</span>
        </li>
        <li class="contact-item">
          <svg class="contact-icon" viewBox="0 0 20 20" aria-hidden="true"><rect x="5" y="2" width="10" height="6" fill="none" stroke="#fff" stroke-width="2"/><rect x="2" y="8" width="16" height="8" fill="#fff"/><rect x="5" y="13" width="10" height="5" fill="#fff" stroke="#333436" stroke-width="1"/></svg>
          <span>482 71 520</span>
        </li>
        <li class="contact-item">
          <svg class="contact-icon" viewBox="0 0 20 20" aria-hidden="true"><rect x="2" y="4" width="16" height="12" fill="none" stroke="#fff" stroke-width="2"/><path d="M2 4l8 7 8-7" fill="none" stroke="#fff" stroke-width="2"/></svg>
          <span>lmoen@brindex.no</span>
        </li>
        <li class="contact-item">
          <svg class="contact-icon" viewBox="0 0 20 20" aria-hidden="true"><circle cx="10" cy="10" r="8" fill="none" stroke="#fff" stroke-width="2"/><path d="M2 10h16M10 2c-4 4-4 12 0 16M10 2c4 4 4 12 0 16" fill="none" stroke="#fff" stroke-width="1.5"/></svg>
          <span>www.brindex.no</span>
        </li>
      </ul>
    </section>

    <section class="holder-panel">
      <p class="holder-name">Lars Moen</p>
      <p class="holder-title">Director</p>
    </section>

    <footer class="company-line">Valto <span class="company-accent">Brindex AS</span>, Kvernlia 14, 3170 Sem</footer>
  </main>
</body>
</html>
```